Brightway Haul & Upkeep Services, are a company that offers a 'one stop shop' pre-move clean up a

I have already selected a logo which I would like on the front of the business cards along with phone numbers, web address and email which are:
0487650392
www.brightwayhaul.com.au
brightwayhaulandupkeep@mailbox.example

On the back of the card I would like to list some of the types of service we offer (clean - move - repairs/maintenance) which are:
CLEAN - windows, gutters, solar panels, driveways/paths, carpets.
MOVE - Small/medium size house/office moves, large item pick-up & delivery, yard clean-up and removal.
General maintenance and repairs.

I would like the blue logo on a gray background.

Thanks

```html
<!DOCTYPE html>
<html lang="en">
<head>
<meta charset="utf-8">
<title>Brightway Haul &amp; Upkeep Services – Business Card</title>
<link rel="stylesheet" href="https://fonts.googleapis.com/css2?family=Open+Sans:wght@400;600;700;800&display=swap">
<style>
  :root {
    --brand-blue: #1f6bb5;
    --ink: #222428;
    --card-white: #ffffff;
    --backdrop: #e6e7e9;
    --card-shadow: 0 6px 18px rgba(0,0,0,0.18);
  }
  * { box-sizing: border-box; margin: 0; padding: 0; }
  html, body {
    width: 1200px; height: 1056px; overflow: hidden;
    background: var(--backdrop);
    font-family: "Open Sans", Arial, sans-serif;
  }
  .canvas { position: relative; width: 1200px; height: 1056px; }

  .card {
    position: absolute; width: 780px; height: 440px;
    background: var(--card-white); border-radius: 36px;
    box-shadow: var(--card-shadow); overflow: hidden;
  }
  .card--front { left: 60px; top: 60px; }
  .card--back { left: 360px; top: 556px; }

  /* Front */
  .front-wave { position: absolute; inset: 0; width: 100%; height: 100%; }
  .company-name {
    position: absolute; left: 78px; top: 88px;
    color: var(--brand-blue); font-weight: 800;
    font-size: 50px; line-height: 1.02; text-transform: uppercase;
    letter-spacing: -0.5px;
  }
  .contact {
    position: absolute; left: 112px; top: 232px;
    color: var(--ink); font-size: 16px; line-height: 26px;
  }
  .contact-row { display: flex; align-items: center; gap: 8px; }
  .contact-row svg { width: 14px; height: 14px; fill: var(--brand-blue); }
  .front-web {
    position: absolute; right: 40px; top: 352px;
    color: var(--card-white); font-size: 22px; line-height: 30px; letter-spacing: 3px;
  }

  /* Back */
  .services-panel {
    position: absolute; left: 50px; top: 110px; width: 690px; height: 176px;
    background: var(--brand-blue); border-radius: 22px;
    color: var(--card-white); text-align: center;
    padding-top: 40px;
  }
  .services-title { font-size: 30px; font-weight: 700; letter-spacing: 3px; margin-bottom: 12px; }
  .services-list { list-style: none; font-size: 23px; font-weight: 600; line-height: 32px; }
  .back-web {
    position: absolute; left: 0; right: 0; top: 322px; text-align: center;
    color: var(--ink); font-size: 27px; letter-spacing: 3px;
  }
</style>
</head>
<body>
<main class="canvas">

  <section class="card card--front" aria-label="Card front">
    <svg class="front-wave" viewBox="0 0 780 440" preserveAspectRatio="none" aria-hidden="true">
      <path d="M0,300 C200,430 420,340 560,262 C650,214 720,198 780,195 L780,440 L0,440 Z" fill="#1f6bb5"/>
      <path d="M70,412 C260,468 470,440 640,427 C700,423 750,421 790,421" fill="none" stroke="#ffffff" stroke-width="6"/>
    </svg>

    <h1 class="company-name">Brightway Haul<br>&amp; Upkeep Services</h1>

    <div class="contact">
      <p class="contact-row">
        <svg viewBox="0 0 24 24"><path d="M6.6 10.8a15.1 15.1 0 0 0 6.6 6.6l2.2-2.2a1 1 0 0 1 1-.25 11.4 11.4 0 0 0 3.6.57 1 1 0 0 1 1 1V20a1 1 0 0 1-1 1A17 17 0 0 1 3 4a1 1 0 0 1 1-1h3.5a1 1 0 0 1 1 1c0 1.25.2 2.45.57 3.6a1 1 0 0 1-.25 1z"/></svg>
        0487650392
      </p>
      <p class="contact-row">
        <svg viewBox="0 0 24 24"><path d="M2 5h20v14H2z M3 6l9 7 9-7" /></svg>
        brightwayhaulandupkeep@mailbox.example
      </p>
    </div>

    <p class="front-web">www.brightwayhaul.com.au</p>
  </section>

  <section class="card card--back" aria-label="Card back">
    <div class="services-panel">
      <h2 class="services-title">Services we offer</h2>
      <ul class="services-list">
        <li>• CLEAN • MOVE</li>
        <li>• GENERAL MAINTENANCE AND REPAIRS.</li>
      </ul>
    </div>
    <p class="back-web">www.brightwayhaul.com.au</p>
  </section>

</main>
</body>
</html>
```